BUSINESS CARD - HALLORAN FIELD SERVICES

I would like to create a business card for my fertilizer spreading business. I would like to incorporate my existing logo and also a description of the services offered. The business card will be given to farmers so must be kept simple but effective. It will also be left in stores so much also be eye catching in order to stand out from other cards.

Target Market(s)

FARMERS

Requirements
Must have
• FRONT OF CARD = EXISTING LOGO + "CUSTOMISED SPREADING" below the logo

REAR Of CARD = SERVICES OFFERED AND CONTACT DETAILS

- Bulk fertilizer including Lime, Gypsum, Manure & Compost
- Granular fertilizer including Single Super, Urea, Gran-am, & Custom Blends
- Modern equipment - Autosteer & Variable Rate Capable
- Friendly & Reliable Service
- Contact Gus: 0417 552 308
Nice to have
• utilize same color scheme as existing logo

```html
<!DOCTYPE html>
<html lang="en">
<head>
<meta charset="utf-8">
<title>Halloran Field Services – Business Card</title>
<link rel="stylesheet" href="https://fonts.googleapis.com/css2?family=Lexend:wght@300;400;500;600&display=swap">
<style>
  :root {
    --backdrop: #adb5bf;
    --card: #ffffff;
    --ink: #58585a;
    --ink-soft: #4a4a4c;
    --accent: #f7941d;
    --on-dark: #ffffff;
  }
  * { box-sizing: border-box; margin: 0; padding: 0; }
  html, body {
    width: 1200px;
    height: 1200px;
    overflow: hidden;
    background: var(--backdrop);
    font-family: "Lexend", sans-serif;
  }
  .canvas { position: relative; width: 1200px; height: 1200px; }

  .card {
    position: absolute;
    left: 264px;
    width: 672px;
    height: 404px;
    background: var(--card);
  }
  .card--rear { top: 172px; }
  .card--front { top: 614px; }

  .brand {
    position: absolute;
    left: 0;
    width: 100%;
    display: flex;
    flex-direction: column;
    align-items: center;
  }
  .brand__mark {
    border-radius: 50%;
    border: 6px solid var(--ink);
  }
  .brand__name {
    color: var(--ink);
    font-weight: 600;
    letter-spacing: 0.01em;
    white-space: nowrap;
  }

  .card--rear .brand { top: 24px; }
  .card--rear .brand__mark { width: 84px; height: 84px; border-width: 5px; }
  .card--rear .brand__name { font-size: 21px; margin-top: 12px; }

  .card--front .brand { top: 92px; }
  .card--front .brand__mark { width: 168px; height: 168px; border-width: 9px; }
  .card--front .brand__name { font-size: 40px; margin-top: 18px; }

  .services {
    position: absolute;
    top: 192px;
    left: 0;
    width: 100%;
    list-style: none;
    text-align: center;
    color: var(--ink-soft);
    font-size: 15.5px;
    font-weight: 300;
    line-height: 21.6px;
  }

  .contact-band {
    position: absolute;
    top: 317px;
    left: 0;
    width: 100%;
    height: 40px;
    background: var(--ink);
    color: var(--on-dark);
    font-size: 17.5px;
    font-weight: 400;
  }
  .contact-band__name {
    position: absolute;
    right: 392px;
    top: 50%;
    transform: translateY(-50%);
  }
  .contact-band__phone {
    position: absolute;
    left: 395px;
    top: 50%;
    transform: translateY(-50%);
  }
  .contact-band__icon {
    position: absolute;
    left: 303px;
    top: -12px;
    width: 64px;
    height: 64px;
    border-radius: 50%;
    background: var(--accent);
    border: 4px solid var(--ink);
    display: flex;
    align-items: center;
    justify-content: center;
  }
  .contact-band__icon svg { width: 30px; height: 30px; }
</style>
</head>
<body>
<main class="canvas">

  <section class="card card--rear" aria-label="Card rear: services and contact">
    <div class="brand">
      <div class="brand__mark"></div>
      <div class="brand__name">HALLORAN FIELD SERVICES</div>
    </div>

    <ul class="services">
      <li>Bulk fertilizer including Lime, Gypsum, Manure &amp; Compos</li>
      <li>Granular fertilizer including Single Super, Urea, Gran-am, &amp; Custom Blends</li>
      <li>Modern equipment - Autosteer &amp; Variable Rate Capable</li>
      <li>Friendly &amp; Reliable Service</li>
    </ul>

    <div class="contact-band">
      <span class="contact-band__name">Contact Gus</span>
      <span class="contact-band__icon" aria-hidden="true">
        <svg viewBox="0 0 24 24" fill="none" stroke="#ffffff" stroke-width="1.8" stroke-linejoin="round">
          <path d="M6.6 3.5l2.6 0.4 1.3 4-1.9 1.4a11 11 0 0 0 6.1 6.1l1.4-1.9 4 1.3 0.4 2.6c-0.3 1.7-1.8 2.9-3.5 2.6C10.4 19.1 4.9 13.6 4 7c-0.3-1.7 0.9-3.2 2.6-3.5z"/>
        </svg>
      </span>
      <span class="contact-band__phone">0417 552 308</span>
    </div>
  </section>

  <section class="card card--front" aria-label="Card front: brand">
    <div class="brand">
      <div class="brand__mark"></div>
      <div class="brand__name">HALLORAN FIELD SERVICES</div>
    </div>
  </section>

</main>
</body>
</html>
```